Chai Tea Company needs a Tea Packaging Box Design

Tea Packaging
Dimensions of the Tea Packaging Box: Height 13 cm; Width 8.5 cm; Depth 7 cm
Individual Teabag Packet/ Sachet: Width 6.5 cm; Length 8.25 cm
We are looking for a new tea packaging design, for our tea business. The material of the box is cardboard. We are also looking for a design that will be on each individual tea bag sachet/packet that goes into the box. This design will be very similar to what you design for the tea packaging box.
Product Info:
Our tea company is called “Velmora Brew”. We sell two types of Chai Tea, once called “Velmora Gold” and one called “Velmora Meadow”. The Velmora Gold has caffeine, while the Velmora Meadow is Naturally Caffeine Free. The Velmora Gold has a black tea base, while the Velmora Meadow has a Rooibos tea base. We will need two tea packaging designs, one for each Chai Tea flavour. The designs for both the teas can be similar, but make sure that you can easily distinguish one from the other (example: make them have different colours or pictures). Both the chai teas, come from the same product line.
Tea Packaging Design:
We are looking for high end tea packaging. We produce high quality teas, and we would like to portray this in our tea packaging. Our teas are made with no artificial flavourings, natural flavourings, or preservatives, so we would also like a natural, organic, high quality look to our tea packaging. Our current logo is a llama. It would be great if you could make the current logo more polished and well made. If you feel that the llama is not well suited or you would like to design the llama differently, we are open to your creative ideas.
General Basic Info:
Keep in mind, we will have both English and French writing on the tea packaging. You do not need to worry about the French writing (we will do the translation), just make sure there is room for it. However, if you feel that you are capable and knowledgeable of incorporating both French and English language into the tea packaging that would be of great help and value.
Back of the Box:
- Will have ingredients and brewing instructions. Basic brewing instructions are: “Add hot water to teabag. Steep for 5-7 minutes, depending on strength preferred. Add milk and your choice of sweetener. Enjoy! See inside panel of box for more detailed instructions”. (The basic brewing instructions, can further be polished or written in a more creative or professional manner).
Front of the Box:
- Will have company name, type of tea, little description of the tea
- 18 teabags
- 54 g (1.9 OZ)
- Should state that this is a product of Alberta, Canada.
Side of the Box:
Any creative wording, slogan, or description about the tea, or whatever you feel would be good on the side of the box.
On the inside flap of the side of the box, there will be detailed instructions on how to brew the tea. These will be different from the simplified brewing instructions on the back of the box. I have attached the advanced brewing instructions as a file. These instructions can further be simplified or reduced to make it easier and cleaner for the consumers to read.
Individual Tea Sachets/ Packets
- These will have a matching look and design of the tea box packaging, except on a smaller scale. Each individual sachet will have the company name, type of tea, little description of the tea in the front of the sachet, while the back will contain the ingredients, and basic brewing instructions.
I have attached a few files, with the dimensions, ingredients, detailed brewing directions, and current logo of the business.
If you have any questions, about the design or packaging please let me know. The winning designer will be required to do a few additional tweaks to finalize the product. Thank you for your time and happy designing!

```html
<!DOCTYPE html>
<html lang="en">
<head>
<meta charset="utf-8">
<title>Velmora Brew – Velmora Gold Tea Box</title>
<link rel="stylesheet" href="https://fonts.googleapis.com/css2?family=Cinzel:wght@500&family=Great+Vibes&family=Josefin+Sans:wght@300;400;600&display=swap">
<style>
  :root {
    --bg: #d9d9d9;
    --paper: #f7f7f5;
    --kraft: #8b6c3c;
    --kraft-dark: #6f5430;
    --ink: #4a6474;
    --ink-soft: #6f8794;
    --llama: #a9c6d6;
    --gold: #9a7a3f;
  }
  * { box-sizing: border-box; margin: 0; padding: 0; }
  html, body { width: 1200px; height: 1000px; overflow: hidden; }
  body {
    background: var(--bg);
    font-family: "Josefin Sans", sans-serif;
    color: var(--ink);
    position: relative;
  }
  .box-face {
    position: absolute;
    top: 180px;
    width: 470px;
    height: 640px;
    display: flex;
    box-shadow: 0 10px 30px rgba(0,0,0,0.18);
  }
  .box-face--back { left: 95px; }
  .box-face--front { left: 635px; }
  .kraft-band {
    width: 60px;
    background: linear-gradient(180deg, var(--kraft), var(--kraft-dark));
  }
  .panel {
    flex: 1;
    background: var(--paper);
    display: flex;
    flex-direction: column;
    align-items: center;
    text-align: center;
    padding: 26px 28px;
  }
  .llama-mark {
    background: linear-gradient(180deg, #c3d8e3, var(--llama));
    border-radius: 6px;
  }
  .brand-name {
    font-family: "Cinzel", serif;
    font-weight: 500;
    color: var(--ink);
    letter-spacing: 1px;
  }
  /* back panel */
  .back .llama-mark { width: 90px; height: 110px; margin-top: 10px; }
  .back .brand-name { font-size: 28px; margin-top: 10px; }
  .back .product-title { font-size: 15px; font-weight: 600; letter-spacing: 1.5px; margin-top: 16px; }
  .back .copy {
    text-align: left;
    width: 100%;
    font-size: 11.5px;
    line-height: 1.45;
    letter-spacing: 0.5px;
    text-transform: uppercase;
    margin-top: 14px;
  }
  .back h3 { font-size: 13px; font-weight: 600; letter-spacing: 1px; margin-top: 14px; text-align: left; width: 100%; }
  .back ul, .back ol { width: 100%; text-align: left; list-style: none; font-size: 10px; line-height: 1.55; letter-spacing: 0.4px; text-transform: uppercase; margin-top: 6px; }
  /* front panel */
  .front .tea-type { display: flex; gap: 14px; align-items: flex-start; font-size: 12px; letter-spacing: 1px; margin-top: 4px; }
  .front .tea-type small { display: block; font-size: 9.5px; color: var(--gold); margin-top: 3px; }
  .front .tea-type .dot { width: 7px; height: 7px; background: var(--ink); margin-top: 4px; }
  .front .product-title { font-family: "Great Vibes", cursive; font-size: 50px; color: var(--ink); line-height: 1; margin-top: 8px; }
  .front .desc { font-size: 12px; letter-spacing: 0.8px; line-height: 1.35; text-transform: uppercase; margin-top: 6px; }
  .front .rule { width: 90%; height: 1px; background: var(--gold); margin: 8px 0; }
  .front .desc-fr { font-size: 10px; font-style: italic; color: var(--gold); line-height: 1.4; text-transform: uppercase; letter-spacing: 0.5px; }
  .front .llama-mark { width: 220px; height: 210px; margin-top: 18px; }
  .front .brand-name { font-size: 34px; margin-top: 10px; }
  .front .count { font-size: 38px; font-weight: 300; color: var(--gold); margin-top: 12px; line-height: 1; }
  .front .count-label { font-size: 14px; letter-spacing: 1px; color: var(--gold); }
  .front .count-fr { font-size: 10px; letter-spacing: 1px; color: var(--gold); }
  .front .notes { font-size: 9px; letter-spacing: 0.6px; text-transform: uppercase; margin-top: 8px; }
  .front .weight { font-size: 12px; letter-spacing: 1px; margin-top: 4px; }
  .front .origin { font-size: 10px; letter-spacing: 1px; margin-top: 2px; }
</style>
</head>
<body>
  <section class="box-face box-face--back">
    <div class="kraft-band"></div>
    <div class="panel back">
      <div class="llama-mark" role="img" aria-label="Llama emblem illustration"></div>
      <div class="brand-name">VELMORA BREW</div>
      <div class="product-title">VELMORA GOLD</div>
      <p class="copy">Chai is a rich blend of strong and flavourful tea, aromatic spices, milk and sugar. Chai is an art that requires all natural ingredients, care and time to prepare.</p>
      <h3>FOR 2 CUPS:</h3>
      <h3>INGREDIENTS:</h3>
      <ul>
        <li>2 cups of water</li>
        <li>2 cups of milk</li>
        <li>2 Velmora Gold tea bags</li>
        <li>4 teaspoons of sugar, or to taste</li>
      </ul>
      <h3>DIRECTIONS:</h3>
      <ol>
        <li>1. Bring water and tea bags to a low boil in a covered pot.</li>
        <li>2. Turn down heat, keep covered and simmer for 5 minutes.</li>
        <li>3. Add milk and sugar, stir and return to a gentle boil.</li>
        <li>4. Turn off heat and let steep for a further 2 to 3 minutes.</li>
        <li>5. Strain into cups and serve hot. Enjoy!</li>
      </ol>
    </div>
    <div class="kraft-band"></div>
  </section>

  <section class="box-face box-face--front">
    <div class="kraft-band"></div>
    <div class="panel front">
      <div class="tea-type">
        <span>CHAI TEA<small>WITH CAFFEINE</small></span>
        <span class="dot"></span>
        <span>THÉ CHAI<small>AVEC LA CAFÉINE</small></span>
      </div>
      <h1 class="product-title">Velmora Gold</h1>
      <p class="desc">An exotic blend of black tea,<br>cardamom, fennel, cloves,<br>ginger and cinnamon</p>
      <div class="rule"></div>
      <p class="desc-fr">Un mélange exotique de thé noir,<br>cardamome, fenouil, clous de girofle,<br>gingembre et cannelle</p>
      <div class="llama-mark" role="img" aria-label="Llama emblem illustration"></div>
      <div class="brand-name">VELMORA BREW</div>
      <div class="count">18</div>
      <div class="count-label">TEA BAGS</div>
      <div class="count-fr">SACHETS DE THÉ</div>
      <div class="notes">No preservatives &amp; no artificial flavours</div>
      <div class="weight">NET WT 54 G (1.9 OZ)</div>
      <div class="origin">PRODUCT OF ALBERTA, CANADA</div>
    </div>
    <div class="kraft-band"></div>
  </section>
</body>
</html>
```